World leading Water filters German made

I am a local Plumbing business who is authorised water filter installer
I want to do a Flyer design double sided targeting niche market for Water Filters.
My company colours are black background with white writing.
( but happy to go into different colours to capture more people )
I want all my stuff, sleek and professional with the same fonts throughout.
Www.brightpipeandboiler.au
Is my website you can see how I do things there.
I want the local business awards finalist logo on the flyer too ( it’ll be in the photo)
This Flyer I want all about health and wellness making big points on water filtration benefits
Massive to included HYDROGEN WATER AND ALKALINE WATER ,
REMOVE FLUORIDE
I don’t know whether to have it with the pre-save branded information I sent over, but I don’t want the company other companies name everywhere
I want the main focus about my company Bright Pipe And Boiler Experts
I want the focus to be about a family owned and run Illawarra local business establish for over 20 years.
Please note I have included a Customer brochure the company has designed so you can see some key points on the second page about the products. I want this a lot more eye-catching and appealing please
Target Market(s)
Health and wellness people
Colors
Designer to choose colors to be used in the design.
Requirements
Must have
- Call Derek 0459 237 816, my website , social media buttons ,
Nice to have
- World leading , health and wellness ,
Should not have
- Any information to lead them away from calling myself , I’m the authorities dealer for clearspring supply but I want to no have as much anout them.

```html
<!DOCTYPE html>
<html lang="en">
<head>
<meta charset="utf-8">
<title>Bright Pipe And Boiler Experts – Water Filtration Flyer</title>
<link href="https://fonts.googleapis.com/css2?family=Montserrat:wght@400;500;600;700;800;900&display=swap" rel="stylesheet">
<style>
  :root{
    --backdrop:#d9d9d9;
    --paper:#ffffff;
    --panel:#f3f3f3;
    --ink:#0d0d0d;
    --red:#e10600;
    --deep-red:#a60000;
    --navy:#15304f;
    --navy-light:#24466b;
    --white:#ffffff;
  }
  *{margin:0;padding:0;box-sizing:border-box}
  html,body{width:1200px;height:2317px;overflow:hidden;background:var(--backdrop)}
  body{position:relative;font-family:'Montserrat',sans-serif;color:var(--ink)}

  .page{position:absolute;background:var(--paper);overflow:hidden}
  .page--front{left:139px;top:85px;width:923px;height:1006px}
  .page--back{left:137px;top:1192px;width:927px;height:1010px}
  .page__art{position:absolute;left:0;top:0}
  .abs{position:absolute}

  /* front */
  .front-panel{left:22px;top:25px;width:560px;height:870px;background:var(--panel)}
  .brand-name{font-weight:800;text-transform:uppercase;color:var(--ink);line-height:1.05;letter-spacing:.5px}
  .brand-name--front{left:50px;top:78px;width:260px;font-size:27px;display:flex;align-items:center;gap:12px}
  .brand-mark{width:18px;height:18px;background:var(--ink);flex:none}
  .award-badge{left:401px;top:61px;width:75px;height:140px;background:var(--deep-red)}
  .headline{left:48px;top:288px;font-weight:900;text-transform:uppercase;line-height:1}
  .headline__big{display:block;font-size:60px;letter-spacing:.5px}
  .headline__mid{display:block;font-size:34px;font-weight:800;margin-top:8px}
  .headline__water{display:block;font-size:95px;color:var(--deep-red);margin-top:4px;letter-spacing:-1px}
  .headline__tail{display:block;font-size:34px;font-weight:800;margin-top:6px}
  .dash{height:5px;display:flex;gap:6px}
  .dash span{display:block;height:5px;border-radius:3px;background:var(--red)}
  .dash span:first-child{width:16px}
  .dash span:last-child{width:50px}
  .dash--front{left:59px;top:561px}
  .subhead{left:48px;top:605px;font-size:34px;font-weight:800;line-height:1.02;text-transform:uppercase}
  .experience{left:48px;top:762px;font-size:32px;font-weight:700;letter-spacing:-1px;text-transform:uppercase;line-height:1.25}
  .experience__years{display:inline-block;background:var(--red);color:var(--white);padding:0 16px 0 8px;margin-right:12px}
  .web-link{color:var(--white);font-weight:500;text-decoration:none;display:flex;align-items:center;gap:14px}
  .web-link--front{left:52px;top:910px;font-size:17px}
  .socials{display:flex;gap:9px}
  .socials--front{left:57px;top:955px}
  .social-btn{width:26px;height:26px;border-radius:3px}
  .social-btn--a{background:#3b5bb5}
  .social-btn--b{background:#e0306f}
  .social-btn--c{background:#c4260f}
  .call-label{color:var(--white);font-weight:700;text-transform:uppercase;letter-spacing:-.5px}
  .call-label--front{left:584px;top:877px;font-size:20px;line-height:1.05}
  .phone{color:var(--white);font-weight:800;letter-spacing:-2px;line-height:1}
  .phone--front{left:584px;top:928px;font-size:53px}
  .phone-icon--front{left:527px;top:935px}

  /* back */
  .benefits-panel{left:0;top:101px;width:553px;height:640px;background:var(--panel);border-radius:0 24px 0 0}
  .benefits-title{left:38px;top:133px;font-size:34px;font-weight:900;text-transform:uppercase}
  .dash--back{left:43px;top:186px}
  .benefit-list{left:43px;top:243px;list-style:none}
  .benefit{display:flex;align-items:center;gap:19px;height:57px;margin-bottom:27px;font-size:26px;font-weight:500;line-height:1}
  .benefit--tall{margin-bottom:33px}
  .benefit__dot{width:57px;height:57px;border-radius:50%;background:radial-gradient(circle at 40% 35%,#f0221b,#b80000);flex:none;box-shadow:0 2px 4px rgba(0,0,0,.25)}
  .contact-box{left:0;top:725px;width:594px;height:200px;background:linear-gradient(90deg,var(--navy),var(--navy-light));border-radius:0 0 24px 0}
  .contact-tab{left:553px;top:695px;width:41px;height:40px;background:var(--navy-light);border-radius:0 28px 0 0}
  .call-label--back{left:129px;top:762px;font-size:15px;font-weight:600}
  .phone--back{left:125px;top:782px;font-size:52px}
  .web-link--back{left:128px;top:845px;font-size:22px;text-decoration:underline}
  .phone-icon--back{left:63px;top:793px}
  .globe-icon--back{left:63px;top:852px}
  .side-info{left:589px;top:225px;width:300px;text-align:center}
  .brand-name--back{font-size:31px;line-height:1.05;display:flex;align-items:center;justify-content:center;gap:12px}
  .tagline{margin-top:46px;font-size:16px;font-weight:800;text-transform:uppercase;line-height:1.05}
  .motto{margin-top:43px;font-size:25px;font-weight:900;text-transform:uppercase;line-height:1}
  .blurb{margin-top:37px;font-size:16.5px;font-weight:500;line-height:1.45;color:#222}
  .socials--back{left:690px;top:696px}
</style>
</head>
<body>

<section class="page page--front" aria-label="Flyer front">
  <div class="abs front-panel"></div>

  <svg class="page__art" width="923" height="1006" viewBox="0 0 923 1006">
    <defs>
      <linearGradient id="photoTone" x1="0" y1="0" x2="1" y2="1">
        <stop offset="0" stop-color="#e7ddd3"/>
        <stop offset=".5" stop-color="#f1ece8"/>
        <stop offset="1" stop-color="#dfe3e6"/>
      </linearGradient>
      <linearGradient id="steel" x1="0" y1="0" x2="1" y2="1">
        <stop offset="0" stop-color="#cfd2d4"/>
        <stop offset=".35" stop-color="#f4f5f6"/>
        <stop offset=".7" stop-color="#a9adb0"/>
        <stop offset="1" stop-color="#dfe1e2"/>
      </linearGradient>
      <linearGradient id="navyBand" x1="0" y1="0" x2="1" y2="0">
        <stop offset="0" stop-color="#15304f"/>
        <stop offset="1" stop-color="#24466b"/>
      </linearGradient>
    </defs>
    <path role="img" aria-label="Photo of a woman drinking a glass of filtered water" d="M635 0 L923 0 L923 870 C640 700 600 300 635 0Z" fill="url(#photoTone)"/>
    <path d="M577 0 L635 0 C600 300 640 700 923 870 L923 895 C600 760 540 350 577 0Z" fill="var(--red)"/>
    <path d="M0 885 L491 885 C470 930 462 970 460 1006 L0 1006Z" fill="url(#navyBand)"/>
    <path d="M473 1006 C478 900 560 830 680 822 C780 818 860 860 923 895 L923 1006Z" fill="url(#navyBand)"/>
    <rect role="img" aria-label="Photo of the clearspring supply stainless steel filtration unit" x="527" y="325" width="342" height="513" rx="8" fill="url(#steel)"/>
  </svg>

  <div class="abs brand-name brand-name--front"><span class="brand-mark"></span>Bright Pipe And Boiler Experts</div>
  <div class="abs award-badge" role="img" aria-label="Local business awards finalist badge"></div>

  <h1 class="abs headline">
    <span class="headline__big">Experience</span>
    <span class="headline__mid">Wellness with our</span>
    <span class="headline__water">Water</span>
    <span class="headline__tail">Filtration solutions</span>
  </h1>

  <div class="abs dash dash--front"><span></span><span></span></div>

  <p class="abs subhead">Discover the<br>power of hydrogen<br>and alkaline water</p>

  <p class="abs experience">Water specialist over<br><span class="experience__years">20 Years</span>Experience</p>

  <a class="abs web-link web-link--front" href="#">
    <svg width="26" height="26" viewBox="0 0 24 24" fill="none" stroke="var(--red)" stroke-width="2"><circle cx="12" cy="12" r="10"/><path d="M2 12h20M12 2c3 3 3 17 0 20M12 2c-3 3-3 17 0 20"/></svg>
    www.brightpipeandboiler.au
  </a>
  <div class="abs socials socials--front">
    <span class="social-btn social-btn--a"></span><span class="social-btn social-btn--b"></span><span class="social-btn social-btn--c"></span>
  </div>

  <p class="abs call-label call-label--front">Call us today<br>for free quotes</p>
  <svg class="abs phone-icon--front" width="36" height="36" viewBox="0 0 24 24" fill="var(--red)"><path d="M6.6 10.8a15 15 0 0 0 6.6 6.6l2.2-2.2a1 1 0 0 1 1-.25 11 11 0 0 0 3.6.6 1 1 0 0 1 1 1V20a1 1 0 0 1-1 1A17 17 0 0 1 3 4a1 1 0 0 1 1-1h3.5a1 1 0 0 1 1 1c0 1.25.2 2.45.6 3.6a1 1 0 0 1-.25 1z"/></svg>
  <p class="abs phone phone--front">0459 237 816</p>
</section>

<section class="page page--back" aria-label="Flyer back">
  <div class="abs benefits-panel"></div>
  <h2 class="abs benefits-title">Our benefits</h2>
  <div class="abs dash dash--back"><span></span><span></span></div>
  <ul class="abs benefit-list">
    <li class="benefit"><span class="benefit__dot"></span>Reduce cancer</li>
    <li class="benefit"><span class="benefit__dot"></span>Relief for eczema sufferers</li>
    <li class="benefit"><span class="benefit__dot"></span>Anti-Aging benefits</li>
    <li class="benefit benefit--tall"><span class="benefit__dot"></span>Reduce the risk of birth<br>defects</li>
    <li class="benefit"><span class="benefit__dot"></span>Relief for asthma sufferers</li>
  </ul>

  <div class="abs contact-tab"></div>
  <div class="abs contact-box"></div>
  <p class="abs call-label call-label--back">Call us today for free quotes</p>
  <svg class="abs phone-icon--back" width="30" height="30" viewBox="0 0 24 24" fill="var(--red)"><path d="M6.6 10.8a15 15 0 0 0 6.6 6.6l2.2-2.2a1 1 0 0 1 1-.25 11 11 0 0 0 3.6.6 1 1 0 0 1 1 1V20a1 1 0 0 1-1 1A17 17 0 0 1 3 4a1 1 0 0 1 1-1h3.5a1 1 0 0 1 1 1c0 1.25.2 2.45.6 3.6a1 1 0 0 1-.25 1z"/></svg>
  <p class="abs phone phone--back">0459 237 816</p>
  <svg class="abs globe-icon--back" width="28" height="28" viewBox="0 0 24 24" fill="none" stroke="var(--red)" stroke-width="2"><circle cx="12" cy="12" r="10"/><path d="M2 12h20M12 2c3 3 3 17 0 20M12 2c-3 3-3 17 0 20"/></svg>
  <a class="abs web-link web-link--back" href="#">www.brightpipeandboiler.au</a>

  <div class="abs side-info">
    <div class="brand-name brand-name--back"><span class="brand-mark"></span>Bright Pipe And Boiler Experts</div>
    <p class="tagline">Your source for clean,<br>healthy water</p>
    <p class="motto">Choose quality,<br>choose local,<br>choose health</p>
    <p class="blurb">Reinforce your commitment to providing world-leading health and wellness solutions through water filtration.</p>
  </div>
  <div class="abs socials socials--back">
    <span class="social-btn social-btn--a"></span><span class="social-btn social-btn--b"></span><span class="social-btn social-btn--c"></span>
  </div>
</section>

</body>
</html>
```